Telecommunications/Power civil contractor needs business card design

Were a new telecommunications/power underground civil contractor that is looking for a new business card design. Our company colours are silver or grey and orange. Feel free to use the white background logo or the black background logo.

Target Market(s)

Local contractors, utility companies, private sector mining/energy companies, developers.

Industry/Entity Type

Telecommunications

Contact Information for Business Card

Each card will need the following info:
Persons name:
Title:
E-mail:
Phone number:
Shop Address:
Mailing Address:

Requirements
Must have
• Each card will need the following info:
• Persons name:
• Title:
• E-mail:
• Phone number:
• Shop Address:
• Mailing Address:

```html
<!DOCTYPE html>
<html lang="en">
<head>
<meta charset="utf-8">
<title>Trenchline Civil Inc – Business Card</title>
<link href="https://fonts.googleapis.com/css2?family=Open+Sans:wght@400;600;700&display=swap" rel="stylesheet">
<style>
  :root {
    --orange: #f0622a;
    --grey: #5a5a5a;
    --silver: #9a9a9a;
    --paper: #ffffff;
    --ink: #111111;
    --backdrop: #e9e7e4;
  }
  * { margin: 0; padding: 0; box-sizing: border-box; }
  html, body { width: 1200px; height: 716px; overflow: hidden; }
  body {
    background: var(--backdrop);
    font-family: "Open Sans", Arial, sans-serif;
    position: relative;
  }
  .card {
    position: absolute;
    top: 215px;
    width: 500px;
    height: 286px;
    border-radius: 4px;
    box-shadow: 0 6px 18px rgba(0,0,0,.18);
    overflow: hidden;
  }
  .card-front { left: 70px; background: var(--paper); }
  .card-back { left: 630px; background: var(--ink); }

  .divider-lines { position: absolute; inset: 0; }

  .person { position: absolute; left: 26px; top: 22px; }
  .person-name { color: var(--orange); font-weight: 700; font-size: 15px; line-height: 1.3; }
  .person-title { color: var(--grey); font-size: 14px; line-height: 1.3; }

  .contact { position: absolute; left: 26px; top: 128px; color: var(--grey); font-size: 10.5px; line-height: 1.6; }
  .contact-row { display: flex; align-items: center; gap: 6px; }
  .contact-icon { width: 11px; height: 11px; flex: none; }

  .brand { position: absolute; display: flex; align-items: center; gap: 9px; }
  .brand-circle { border-radius: 50%; border: 3px solid var(--orange); flex: none; }
  .brand-name { color: var(--orange); font-weight: 700; letter-spacing: .5px; line-height: 1.05; text-transform: uppercase; }

  .card-front .brand { left: 262px; top: 140px; }
  .card-front .brand-circle { width: 40px; height: 40px; }
  .card-front .brand-name { font-size: 19px; }

  .card-back .brand { left: 50%; top: 50%; transform: translate(-50%, -50%); }
  .card-back .brand-circle { width: 60px; height: 60px; border-color: var(--silver); }
  .card-back .brand-name { font-size: 24px; }
</style>
</head>
<body>

<section class="card card-front" aria-label="Business card front">
  <svg class="divider-lines" width="500" height="286" viewBox="0 0 500 286" aria-hidden="true">
    <path d="M0 82 H262 Q290 82 300 58 L325 0" fill="none" stroke="var(--orange)" stroke-width="3"/>
    <path d="M0 106 H178 Q200 106 200 128 V286" fill="none" stroke="var(--grey)" stroke-width="3"/>
  </svg>

  <div class="person">
    <p class="person-name">Morgan Hale</p>
    <p class="person-title">Managing Director</p>
  </div>

  <div class="contact">
    <p>N. 42 Ridge Road,</p>
    <p>Suite 200, Boise, ID 83701</p>
    <p class="contact-row">
      <svg class="contact-icon" viewBox="0 0 12 12" aria-hidden="true"><circle cx="6" cy="6" r="6" fill="var(--orange)"/><path d="M4 3.2 L5.2 4.8 L4.6 5.6 Q5.4 7 6.6 7.6 L7.3 7 L8.8 8.2 L8 9.2 Q5 8.8 3 4.2 Z" fill="#fff"/></svg>
      555.010.248
    </p>
    <p class="contact-row">
      <svg class="contact-icon" viewBox="0 0 12 12" aria-hidden="true"><circle cx="6" cy="6" r="6" fill="var(--orange)"/><rect x="3" y="4" width="6" height="4.2" fill="none" stroke="#fff" stroke-width=".9"/><path d="M3 4 L6 6.4 L9 4" fill="none" stroke="#fff" stroke-width=".9"/></svg>
      info@trenchlinecivil.com
    </p>
  </div>

  <div class="brand">
    <span class="brand-circle"></span>
    <p class="brand-name">Trenchline<br>Civil Inc</p>
  </div>
</section>

<section class="card card-back" aria-label="Business card back">
  <div class="brand">
    <span class="brand-circle"></span>
    <p class="brand-name">Trenchline<br>Civil Inc</p>
  </div>
</section>

</body>
</html>
```